Hybrid Seed corn and Soybean Sales business needs a website.

We here at "KW Grain" feel that we need a website to show a very professional side to our customer base. Although no actual ordering will take place on this website, we would like to put Plot and field trail data on the website. Along with a brief page for each of our hybrids and a place for customers to sign up for a newsletter. The company we sell hybrids for is MolvanGrain.com... Im not sure how this process works as far as myself updating the information or having the data actually put on the website, but feel free to contact me if you need the information. I will attach the logo for the company, (KW Grain).

Target Market(s)

Farmers, "Producers", Corn and soybean production

Industry/Entity Type

Business

Coding

Coded - Design and coding required

Number of Pages Required

5+ page

Colors
f78f20
ffffff

Requirements
Nice to have
• Similar layout to http://www.molvangrain.com/
• And it would be nice to incorporate our story into the website
• http://www.molvangrain.com/our-story/molvan-today/

```html
<!DOCTYPE html>
<html lang="en">
<head>
<meta charset="utf-8">
<title>KW Grain – Hybrid Seeds</title>
<link href="https://fonts.googleapis.com/css2?family=Arimo:wght@400;700&family=Open+Sans:wght@400;600&display=swap" rel="stylesheet">
<style>
:root{
  --orange:#f78f20;
  --orange-deep:#e5691a;
  --orange-dark:#c9520e;
  --green:#5f9a0f;
  --amber:#e8960e;
  --red:#ee1c2e;
  --ink:#333;
  --muted:#555;
  --peach:#fbdcc0;
  --peach-line:#efc39a;
  --white:#fff;
  --rule:#d9d9d9;
  --footer-top:#4a4a4a;
  --footer-bottom:#2c2c2c;
}
*{box-sizing:border-box;margin:0;padding:0}
html,body{width:674px;height:1200px;overflow:hidden}
body{position:relative;background:var(--white);font-family:"Open Sans",sans-serif;color:var(--ink)}
.abs{position:absolute}
.top-line{left:0;top:0;width:674px;height:3px;background:var(--orange-deep)}
.brand{left:55px;top:22px;display:flex;align-items:center;gap:8px;font-family:"Arimo",sans-serif;font-weight:700;font-size:24px;color:var(--orange-deep);text-decoration:none}
.brand-dot{width:14px;height:14px;border-radius:50%;background:var(--green)}
.search{left:532px;top:25px;width:113px;height:22px;border:1px solid #cfcfcf;display:flex;align-items:center;justify-content:space-between;padding:0 7px;font-size:7px;color:#999;background:var(--white)}
.hero{left:0;top:85px;width:674px;height:270px;background:radial-gradient(ellipse at 55% 35%,#d9a55a 0%,#b07a32 40%,#6b4516 80%,#4a2e0e 100%)}
.nav{left:29px;top:69px;width:616px;height:32px;display:flex;background:linear-gradient(#f08324,#e0661a);z-index:2}
.nav a{flex:1;display:flex;align-items:center;justify-content:center;font-family:"Arimo",sans-serif;font-size:8px;color:var(--white);text-decoration:none;border-right:1px solid #f4a060}
.nav a:last-child{border-right:none}
.nav a.active{color:#c9f03a}
.hero-title{left:55px;top:177px;font-family:"Arimo",sans-serif;font-weight:700;font-size:25px;color:var(--white)}
.hero-text{left:56px;top:216px;width:290px;font-family:"Arimo",sans-serif;font-size:7.5px;line-height:16px;color:var(--white)}
.arrow{top:205px}
.welcome{left:0;top:393px;width:674px;text-align:center;font-family:"Arimo",sans-serif;font-size:18px;color:var(--ink)}
.intro{left:95px;top:428px;width:484px;text-align:center;font-size:7.4px;line-height:16px;color:var(--muted)}
.card{top:531px;width:128px;height:191px;text-align:center}
.card .badge{position:absolute;left:36px;top:-28px;width:56px;height:56px;border-radius:50%;border:2px solid rgba(255,255,255,.5)}
.card h3{position:absolute;left:0;top:41px;width:128px;font-family:"Arimo",sans-serif;font-weight:700;font-size:11px;color:var(--white)}
.card p{position:absolute;left:10px;top:59px;width:108px;font-size:6.6px;line-height:12px}
.card .photo{position:absolute;left:0;top:90px;width:128px;height:101px}
.c1{left:55px;background:var(--orange-deep)}.c1 .badge{background:var(--orange-deep)}.c1 p{color:#8a1010}
.c1 .photo{background:radial-gradient(circle,#b0202a,#7a0f18)}
.c2{left:200px;background:var(--green)}.c2 .badge{background:var(--green)}.c2 p{color:#f3e03a}
.c2 .photo{background:radial-gradient(circle,#f0c050,#d08a1a)}
.c3{left:345px;background:var(--amber)}.c3 .badge{background:var(--amber)}.c3 p{color:#8a1010}
.c3 .photo{background:radial-gradient(circle,#9fd060,#4f8a25)}
.c4{left:490px;background:var(--red)}.c4 .badge{background:var(--red)}.c4 p{color:#ffa020}
.c4 .photo{background:radial-gradient(circle,#ffd030,#f09a10)}
.rule{left:55px;width:564px;height:1px;background:var(--rule)}
.about-title{left:55px;top:771px;font-family:"Arimo",sans-serif;font-size:12.5px;color:var(--ink)}
.video{left:56px;top:808px;width:154px;height:108px;background:radial-gradient(circle at 35% 70%,#f6b020 0%,#b84a10 30%,#3a1a08 65%,#111 100%)}
.about-text{font-size:7.2px;line-height:16px;color:var(--muted)}
.about-text.side{left:220px;top:806px;width:196px}
.about-text.full{left:56px;top:918px;width:360px}
.btn{display:flex;align-items:center;justify-content:center;font-family:"Arimo",sans-serif;font-weight:700;font-size:8.5px;color:var(--white);background:linear-gradient(#ee7a22,#d4581a);border:1px solid var(--orange-dark);border-radius:2px}
.read-more{left:55px;top:981px;width:72px;height:21px}
.newsletter{left:452px;top:774px;width:167px;height:233px;background:var(--peach);border:1px solid var(--peach-line);border-radius:2px}
.newsletter h4{position:absolute;left:0;top:14px;width:100%;text-align:center;font-family:"Arimo",sans-serif;font-weight:400;font-size:12px;color:var(--ink)}
.newsletter label{position:absolute;left:16px;font-family:"Arimo",sans-serif;font-size:6.8px;color:var(--ink)}
.newsletter .field{position:absolute;left:59px;width:96px;height:20px;background:#fde6d2;border:1px solid #f0c8a2}
.sign-in{left:53px;top:205px;width:60px;height:20px;position:absolute}
.partners{left:55px;top:1050px;width:564px;height:50px;display:flex;align-items:center;justify-content:space-around;font-family:"Arimo",sans-serif;font-weight:700}
.partner{display:flex;align-items:center;gap:6px;font-size:15px}
.partner i{display:block;width:12px;height:12px}
.footer{left:0;top:1111px;width:674px;height:89px;background:linear-gradient(var(--footer-top),var(--footer-bottom))}
.social{left:282px;top:1127px;display:flex;gap:7px}
.social span{width:22px;height:22px;border:1.5px solid var(--orange);border-radius:50%}
.foot-links{left:0;top:1157px;width:674px;text-align:center;font-size:7.2px;color:var(--white)}
.copy{left:0;top:1176px;width:674px;text-align:center;font-size:7.2px;color:var(--white)}
.copy b{font-weight:400;color:var(--orange)}
</style>
</head>
<body>
<div class="abs top-line"></div>
<a class="abs brand" href="#"><span class="brand-dot"></span>KW Grain</a>
<div class="abs search">Search
  <svg width="9" height="9" viewBox="0 0 10 10"><circle cx="4" cy="4" r="3" fill="none" stroke="#e5691a" stroke-width="1.6"/><line x1="6.3" y1="6.3" x2="9" y2="9" stroke="#e5691a" stroke-width="1.8"/></svg>
</div>

<div class="abs hero" role="img" aria-label="Golden wheat field at sunset"></div>
<nav class="abs nav">
  <a class="active" href="#">HOME</a><a href="#">OUR STORY</a><a href="#">FRIENDS</a><a href="#">PRODUCTS</a><a href="#">EVENTS &amp; GETAWAYS</a><a href="#">CONTACT</a>
</nav>
<h1 class="abs hero-title">HYBRID SEEDS</h1>
<p class="abs hero-text">Lorem Ipsum is simply dummy text of the printing and typesetting industry. Lorem Ipsum has been the industry's standard dummy text ever since the 1500s, when an unknown printer took a galley .</p>
<svg class="abs arrow" style="left:13px" width="14" height="22" viewBox="0 0 14 22"><polyline points="11,2 3,11 11,20" fill="none" stroke="#fff" stroke-width="2.5"/></svg>
<svg class="abs arrow" style="left:643px" width="14" height="22" viewBox="0 0 14 22"><polyline points="3,2 11,11 3,20" fill="none" stroke="#fff" stroke-width="2.5"/></svg>

<h2 class="abs welcome">WELCOME TO KW GRAIN</h2>
<p class="abs intro">Contrary to popular belief, Lorem Ipsum is not simply random text. It has roots in a piece of classical Latin literature from 45 BC, making it over 2000 years old. Daniel Whitford, a Latin professor at Ashford Valley College in Virginia, looked up one of the more obscure Latin words, consectetur, from a Lorem Ipsum passage, and going through the cites .</p>

<div class="abs card c1"><div class="badge"></div><h3>HYBRID SEEDS</h3><p>Contrary to popular belief Lorem Ipsum is not simply Latin.</p><div class="photo" role="img" aria-label="Close-up of red hybrid seeds"></div></div>
<div class="abs card c2"><div class="badge"></div><h3>CORN</h3><p>Contrary to popular belief Lorem Ipsum is not simply Latin.</p><div class="photo" role="img" aria-label="Close-up of dried corn kernels"></div></div>
<div class="abs card c3"><div class="badge"></div><h3>SOYA BEAN</h3><p>Contrary to popular belief Lorem Ipsum is not simply Latin.</p><div class="photo" role="img" aria-label="Close-up of green soya beans"></div></div>
<div class="abs card c4"><div class="badge"></div><h3>SWEET CORN</h3><p>Contrary to popular belief Lorem Ipsum is not simply Latin.</p><div class="photo" role="img" aria-label="Close-up of yellow sweet corn kernels"></div></div>

<div class="abs rule" style="top:752px"></div>

<h2 class="abs about-title">ABOUT US</h2>
<div class="abs video" role="img" aria-label="Video still of a field at sunset with play button"></div>
<svg class="abs" style="left:123px;top:843px" width="20" height="20" viewBox="0 0 20 20"><circle cx="10" cy="10" r="8.5" fill="rgba(0,0,0,.4)" stroke="#fff" stroke-width="1.5"/><polygon points="8,6 14,10 8,14" fill="#fff"/></svg>
<p class="abs about-text side">Lorem Ipsum is simply dummy text of the printing and typesetting industry. Lorem Ipsum has been the industry's standard dummy text ever since the 1500s, when an unknown printer took a galley of type and scrambled it to make a type specimen book. It has survived not only five centuries, but also the leap into electronic typesetting, remaining essentially unchanged Lorem Ipsum is simply.</p>
<p class="abs about-text full">Lorem Ipsum has been the industry's standard dummy text ever since the 1500s, when an unknown printer took a galley of type and scrambled it to make a type specimen book. It has survived not only five centuries, but also the leap into electronic typesetting, remaining essentially unchanged.</p>
<a class="abs btn read-more" href="#">READ MORE</a>

<form class="abs newsletter">
  <h4>NEWSLETTER</h4>
  <label style="top:56px">NAME :</label><div class="field" style="top:50px"></div>
  <label style="top:90px">EMAIL :</label><div class="field" style="top:84px"></div>
  <label style="top:124px">PH NO :</label><div class="field" style="top:118px"></div>
  <label style="top:157px">MESSAGE :</label><div class="field" style="top:151px;height:42px"></div>
  <div class="btn sign-in">SIGN IN</div>
</form>

<div class="abs rule" style="top:1035px"></div>

<div class="abs partners">
  <div class="partner" style="color:#1a6e7a"><i style="background:#2f9a3a"></i>Verdant</div>
  <div class="partner" style="color:#222"><i style="background:#e0101e"></i>Harlow AgriSciences</div>
  <div class="partner" style="color:#222"><i style="background:var(--orange)"></i>Molvan</div>
</div>

<footer class="abs footer"></footer>
<div class="abs social" aria-label="Social links"><span></span><span></span><span></span><span></span></div>
<p class="abs foot-links">Home / About Us / Sitemap / Products / Contact Us</p>
<p class="abs copy">© 2015 <b>KW Grain</b>. All rights reserved.</p>
</body>
</html>
```